Sales presentation introduction for Finance and Tech firms

Our business is two fold - 1) recruitment 2) consultancy. We would like a one or two page template that we can use to send to potential clients. The template will ideally be the same for the recruitment and consultancy side. We need to be able to edit the template to enter text.

I have attached our logo so you can see what we currently use on Corvella.

Sector is financial services and technology. We do not intent to have lots of text but the layout/images/designs to be used should cover some of page in a way that it takes up some space to avoid having to write lot of text.

Open to colour suggestions.

Please look at the attached word doc to see the text I would like for the two presentations.

Happy to answer questions.

Target Market(s)

Directors

Industry/Entity Type

Finance and tech companies

Colors
0094D4
00A9DD
6FCCEA
C7EBF8
E9F6FB

Requirements
Must have
• Editable text

```html
<!DOCTYPE html>
<html lang="en">
<head>
<meta charset="utf-8">
<title>Veritane Consultancy – Two Page Introduction</title>
<link href="https://fonts.googleapis.com/css2?family=Montserrat:ital,wght@0,300;0,400;0,700;0,800;1,700&family=Jost:wght@300;400&family=Arimo:wght@400&display=swap" rel="stylesheet">
<style>
  :root{
    --brand-blue:#1a5aa8;
    --band-blue:#1d5fae;
    --sheet-blue:#1f78c6;
    --sky:#6fcceA;
    --ice:#c7ebf8;
    --mist:#e9f6fb;
    --ink:#222428;
    --white:#ffffff;
    --backdrop:#e7e8ea;
  }
  *{box-sizing:border-box;margin:0;padding:0}
  html,body{width:1200px;height:900px;overflow:hidden}
  body{background:var(--backdrop);position:relative;font-family:"Arimo",Arial,sans-serif;color:var(--ink)}

  .page{position:absolute;top:73px;width:560px;height:754px;overflow:hidden;box-shadow:0 2px 10px rgba(0,0,0,.12)}
  .page--front{left:27px;background:var(--white)}
  .page--back{left:613px;background:linear-gradient(170deg,#2a86cf 0%,var(--sheet-blue) 45%,#1a64b4 100%)}

  /* front: hero */
  .hero{position:absolute;left:0;top:0;width:560px;height:350px;background:linear-gradient(180deg,var(--mist) 0%,var(--ice) 60%,#ffffff 100%)}
  .hero-photo{position:absolute;left:240px;top:0;width:320px;height:350px;
    background:linear-gradient(90deg,rgba(255,255,255,0) 0%,rgba(120,140,190,.55) 30%,rgba(70,90,150,.8) 65%,rgba(150,110,140,.75) 100%);
    -webkit-mask-image:linear-gradient(180deg,#000 75%,transparent 100%);mask-image:linear-gradient(180deg,#000 75%,transparent 100%)}
  .hero-band{position:absolute;left:0;top:191px;width:560px;height:134px;
    background:linear-gradient(90deg,var(--band-blue) 0%,var(--band-blue) 50%,rgba(29,95,174,.35) 85%,rgba(29,95,174,0) 100%)}
  .hero-word{position:absolute;color:var(--white);white-space:nowrap;line-height:1;font-family:"Montserrat",sans-serif}
  .hero-word--light{font-weight:300;color:rgba(255,255,255,.92)}
  .hero-word--bold{font-weight:800}
  .w-fixed{left:248px;top:20px;font-size:33px}
  .w-income{left:248px;top:52px;font-size:33px}
  .w-ledger{left:160px;top:94px;font-size:44px;color:rgba(255,255,255,.85)}
  .w-workflow{left:48px;top:135px;font-size:22px}
  .w-mis{left:176px;top:135px;font-size:20px}
  .w-management{left:108px;top:154px;font-size:22px}
  .w-equity{left:280px;top:134px;font-size:50px}
  .w-trading{left:0;top:178px;font-size:25px;color:rgba(255,255,255,.8)}
  .w-xml{left:284px;top:179px;font-size:22px}
  .brand-name{position:absolute;font-family:"Jost",sans-serif;font-weight:400;color:#4a4d55;letter-spacing:.5px}
  .brand-name--hero{left:27px;top:72px;font-size:26px}
  .tagline{position:absolute;left:50px;top:208px;width:230px;font-family:"Montserrat",sans-serif;font-style:italic;font-weight:700;font-size:13.4px;line-height:17.4px;color:var(--white)}

  /* front: intro */
  .intro-title{position:absolute;left:71px;top:356px;line-height:1}
  .intro-title .name{display:block;font-family:"Jost",sans-serif;font-size:26px;color:var(--ink)}
  .intro-title .service{display:block;font-family:"Montserrat",sans-serif;font-weight:800;font-size:27px;color:var(--brand-blue);margin-top:3px}
  .intro-copy{position:absolute;left:71px;top:440px;width:425px;font-size:10.2px;line-height:14px}
  .intro-copy p+p{margin-top:10px}
  .services{position:absolute;top:568px;list-style:none;font-size:10.2px;line-height:14.2px}
  .services li{padding-left:17px;position:relative}
  .services li::before{content:"✓";position:absolute;left:0;top:0;font-size:9px}
  .services--a{left:93px}
  .services--b{left:293px}

  .footer{position:absolute;left:0;top:694px;width:560px;height:60px;background:var(--band-blue)}
  .brand-name--footer{left:240px;top:20px;font-size:13px;color:var(--white)}
  .contact{position:absolute;left:309px;top:14px;color:var(--white);font-size:9.4px;line-height:17px}
  .contact-row{display:flex;gap:12px;align-items:center}
  .contact-item{display:flex;align-items:center;gap:5px}
  .contact-item svg{width:8px;height:8px}

  /* back */
  .back-photo{position:absolute;left:0;top:470px;width:560px;height:284px;
    background:linear-gradient(160deg,rgba(31,120,198,0) 0%,rgba(110,150,205,.55) 40%,rgba(150,170,215,.75) 70%,rgba(180,150,190,.7) 100%);
    -webkit-mask-image:linear-gradient(180deg,transparent 0%,#000 30%);mask-image:linear-gradient(180deg,transparent 0%,#000 30%)}
  .brand-name--back{left:37px;top:72px;font-size:22px;color:var(--white)}
  .rule{position:absolute;left:154px;top:94px;width:313px;height:1px;background:rgba(255,255,255,.6)}
  .offer{position:absolute;left:154px;width:315px;color:var(--white)}
  .offer h3{font-family:"Montserrat",sans-serif;font-weight:800;font-size:12px;margin-bottom:3px}
  .offer:first-of-type h3{font-size:13px}
  .offer p{font-size:9.8px;line-height:14px}
  .offer--strategy{top:125px}
  .offer--change{top:227px}
  .offer--it{top:341px}
  .offer--org{top:427px}
  .offer-icon{position:absolute;left:89px;width:38px;height:38px;fill:none;stroke:var(--white);stroke-width:1.6;stroke-linecap:round;stroke-linejoin:round}
  .icon-strategy{top:150px}
  .icon-change{top:253px}
  .icon-it{top:351px}
  .icon-org{top:440px}
</style>
</head>
<body>

<section class="page page--front">
  <div class="hero">
    <div class="hero-photo" role="img" aria-label="Business professionals walking through a city office with market chart overlays"></div>
    <div class="hero-band"></div>
    <span class="hero-word hero-word--bold w-fixed">FIXED</span>
    <span class="hero-word hero-word--bold w-income">INCOME</span>
    <span class="hero-word hero-word--light w-ledger">LEDGER</span>
    <span class="hero-word hero-word--light w-workflow">WORKFLOW</span>
    <span class="hero-word hero-word--bold w-mis">MIS</span>
    <span class="hero-word hero-word--light w-management">MANAGEMENT</span>
    <span class="hero-word hero-word--bold w-equity">EQUITY</span>
    <span class="hero-word hero-word--light w-trading">TRADING PLATFORMS</span>
    <span class="hero-word hero-word--bold w-xml">XML</span>
    <span class="brand-name brand-name--hero">VERITANE</span>
    <p class="tagline">A partner who brings new and innovative ideas to the table, through extensive industry experience and knowledge. Veritane will ensure you are prepared for growth.</p>
  </div>

  <h1 class="intro-title"><span class="name">VERITANE</span><span class="service">CONSULTANCY</span></h1>

  <div class="intro-copy">
    <p>Veritane E2E is a bespoke consultancy firm that specialises in buy side investment. Through an industry based consultative approach we assist our clients in preparing for, and facilitating, long term growth. Working closely with our clients we combine innovative thinking and breakthrough technologies to accelerate progress and, together, achieve enduring results.</p>
    <p>Experienced in successfully delivering change for global organisations as well as assisting smaller firms during their growth phase. Veritane will work with you create a workable model and ensure successful delivery of the project.</p>
  </div>

  <ul class="services services--a">
    <li>Order Management and Trading</li>
    <li>Investment and Research</li>
    <li>Static, Pricing and Benchmark Data</li>
    <li>CRM/ Onboarding</li>
    <li>Performance, Risk and Attribution</li>
  </ul>
  <ul class="services services--b">
    <li>Client and Regulatory Reporting</li>
    <li>Compliance</li>
    <li>Finance and Accounting</li>
    <li>Middle and Back Office</li>
  </ul>

  <footer class="footer">
    <span class="brand-name brand-name--footer">VERITANE</span>
    <div class="contact">
      <div class="contact-item">
        <svg viewBox="0 0 10 10"><circle cx="5" cy="5" r="5" fill="#fff"/><circle cx="5" cy="4.3" r="1.6" fill="#1d5fae"/></svg>
        <span>14 Harbor Lane, Springfield, NJ 07081</span>
      </div>
      <div class="contact-row">
        <div class="contact-item">
          <svg viewBox="0 0 10 10"><circle cx="5" cy="5" r="5" fill="#fff"/><path d="M3.2 2.8l1 1-.6.7a4 4 0 0 0 1.9 1.9l.7-.6 1 1-.8.9C4.8 7.4 2.6 5.2 2.4 3.6z" fill="#1d5fae"/></svg>
          <span>555-010-2468</span>
        </div>
        <div class="contact-item">
          <svg viewBox="0 0 10 10"><circle cx="5" cy="5" r="5" fill="#fff"/><path d="M2.6 5.2l4.8-2.4-1.2 4.8-1.3-1.3z" fill="#1d5fae"/></svg>
          <span>support@veritane.com</span>
        </div>
      </div>
    </div>
  </footer>
</section>

<section class="page page--back">
  <div class="back-photo" role="img" aria-label="Colleagues meeting by an office window overlooking a city skyline"></div>
  <span class="brand-name brand-name--back">VERITANE</span>
  <div class="rule"></div>

  <svg class="offer-icon icon-strategy" viewBox="0 0 38 38"><circle cx="19" cy="9" r="5"/><path d="M17 14v3h4v-3M19 1v1.5M12 4l1 1M26 4l-1 1"/><circle cx="9" cy="25" r="2.5"/><circle cx="19" cy="25" r="2.5"/><circle cx="29" cy="25" r="2.5"/><path d="M5 33a4 4 0 0 1 8 0zM15 33a4 4 0 0 1 8 0zM25 33a4 4 0 0 1 8 0z"/></svg>
  <svg class="offer-icon icon-change" viewBox="0 0 38 38"><circle cx="19" cy="13" r="5"/><path d="M19 3v3M19 20v3M9 13h3M26 13h3M12 6l2 2M24 18l2 2M26 6l-2 2M14 18l-2 2"/><path d="M4 35v-6a3 3 0 0 1 6 0v6M14 35v-6a3 3 0 0 1 6 0v6M24 35v-6a3 3 0 0 1 6 0v6"/></svg>
  <svg class="offer-icon icon-it" viewBox="0 0 38 38"><rect x="5" y="12" width="22" height="15" rx="1"/><path d="M2 31h28"/><circle cx="26" cy="10" r="5"/><path d="M26 3v2M26 15v2M19 10h2M31 10h2"/></svg>
  <svg class="offer-icon icon-org" viewBox="0 0 38 38"><circle cx="9" cy="7" r="3"/><circle cx="28" cy="9" r="4"/><rect x="5" y="15" width="20" height="14" rx="1"/><path d="M9 25v-4M13 25v-6M17 25v-3M21 25v-7M3 33h24"/></svg>

  <article class="offer offer--strategy">
    <h3>Business Strategy</h3>
    <p>Veritane will help you create a business strategy tailored to your requirements. Ensuring each business process is defined and taken into account allows for a successful design. Creating and implementing an operating model that takes into account budget, resources, culture and your company's vision.</p>
  </article>
  <article class="offer offer--change">
    <h3>Change management</h3>
    <p>Veritane works with clients to deliver bespoke change initiatives. Rigorous business analysis and risk management allows for successful change initiatives. We work with you throughout the complete process, to ensure that delivery is based on value. Transition phases are challenging aspects of change initiatives which is why our team manage all transitions and the risk they carry.</p>
  </article>
  <article class="offer offer--it">
    <h3>IT transformation</h3>
    <p>Veritane is widely experienced in a range of technologies. We help with the implementation of software provider or design and develop bespoke services. Covering front to back office the team specialises in full project lifecycle from feasibility through to implementation.</p>
  </article>
  <article class="offer offer--org">
    <h3>Organisational structure</h3>
    <p>Veritane works with clients to improve resource capability and strategic partnerships. Acting as an extension of the HR function, we analyse business processes and ensure that our clients have the ability to manage changing workforce demands.</p>
  </article>
</section>

</body>
</html>
```